DANCE STUDIO RECITAL FLYER DESIGN 2022

I am looking for a flyer for a dance recital that encapsulates the theme of the flyer. The rhetorical answer to "Where the River Bends Home..." is Hold Me Near but I would like this to be inferred in the design of the flyer. I am looking for something uplifting and positive through the design...I don't know what I am looking for but it needs to be vibrant, heartwarming, and emotional...maybe the world can be dipped in a heart or something with butterflies???

Here are the details...

Brightwing Dance Studio presents
Our 11th Annual Recital, "Where The River Bends Home..."
Saturday, June 25, at 4 pm
Kestrel Ridge High School 31857 Marlow Road
Novi, Mi 48291

```html
<!DOCTYPE html>
<html lang="en">
<head>
<meta charset="utf-8">
<title>Brightwing Dance Studio – 11th Annual Recital</title>
<link rel="stylesheet" href="https://fonts.googleapis.com/css2?family=Cinzel:wght@500&family=Oswald:wght@700&family=Kaushan+Script&family=Roboto+Slab:wght@700&family=Fira+Sans:wght@700&display=swap">
<style>
  :root {
    --stage: #4b4b4d;
    --paper-top: #ffffff;
    --paper-bottom: #e9edf2;
    --gold: #dba33b;
    --gold-soft: #f6d36b;
    --maroon: #96113d;
    --rust: #8e3418;
    --crimson: #b3174a;
    --ribbon: #d3121c;
    --ribbon-deep: #a5000f;
    --date-yellow: #fdd57c;
    --ink: #111111;
  }
  * { margin: 0; padding: 0; box-sizing: border-box; }
  html, body { width: 1200px; height: 1200px; overflow: hidden; background: var(--stage); }
  .flyer {
    position: absolute; left: 197px; top: 30px;
    width: 805px; height: 1140px; overflow: hidden;
    background: linear-gradient(180deg, var(--paper-top) 0%, var(--paper-top) 55%, var(--paper-bottom) 100%);
  }
  .butterflies {
    position: absolute; top: 48px; width: 172px; height: 344px;
    background: radial-gradient(ellipse at center, rgba(246,211,107,.55) 0%, rgba(246,211,107,.18) 55%, rgba(246,211,107,0) 75%);
  }
  .butterflies--left { left: 38px; }
  .butterflies--right { left: 595px; }
  .brand {
    position: absolute; top: 34px; left: 0; width: 100%; text-align: center;
  }
  .brand__dot {
    display: block; width: 52px; height: 52px; margin: 0 auto 26px;
    border-radius: 50%; background: var(--maroon);
  }
  .brand__name {
    font-family: "Cinzel", serif; font-weight: 500; font-size: 32px;
    color: var(--gold); letter-spacing: 1px;
  }
  .presents {
    position: absolute; top: 222px; left: 0; width: 100%; text-align: center;
    font-family: "Fira Sans", sans-serif; font-weight: 700; font-size: 22px;
    letter-spacing: 6px; color: var(--gold);
  }
  .recital-title {
    position: absolute; top: 262px; left: 0; width: 100%; text-align: center;
    font-family: "Kaushan Script", cursive; line-height: 1.15;
  }
  .recital-title__ordinal { display: block; font-size: 54px; color: var(--maroon); }
  .recital-title__name { display: block; font-size: 58px; color: var(--rust); }
  .ribbon-art {
    position: absolute; left: 0; top: 420px; width: 805px; height: 600px;
    background:
      radial-gradient(ellipse 42% 38% at 50% 42%, #ffffff 0%, #f5f5f7 60%, rgba(245,245,247,0) 100%),
      radial-gradient(ellipse 62% 58% at 52% 45%, rgba(211,18,28,0) 55%, rgba(211,18,28,.55) 70%, rgba(165,0,15,.25) 85%, rgba(165,0,15,0) 100%),
      linear-gradient(160deg, rgba(255,255,255,0) 55%, rgba(211,18,28,.35) 75%, rgba(255,255,255,0) 95%);
  }
  .theme {
    position: absolute; top: 572px; left: 0; width: 100%; text-align: center;
    font-family: "Oswald", sans-serif; font-weight: 700; font-size: 60px;
    line-height: 78px; text-transform: uppercase; letter-spacing: -1px;
  }
  .theme__line1 { display: block; color: var(--rust); }
  .theme__line2 { display: block; color: var(--maroon); }
  .date-card {
    position: absolute; left: 48px; top: 970px; width: 338px; height: 139px;
    border: 2px solid var(--maroon); border-radius: 6px; overflow: hidden;
    background: var(--date-yellow); font-family: "Roboto Slab", serif; font-weight: 700;
    text-align: center;
  }
  .date-card__day {
    position: relative; height: 50px; background: var(--maroon);
    color: #fff6e0; font-size: 29px; line-height: 50px;
  }
  .date-card__day svg { position: absolute; top: 13px; }
  .date-card__date { font-size: 38px; color: var(--ink); line-height: 50px; padding-top: 2px; }
  .date-card__rule { height: 1px; margin: 0 22px; background: rgba(150,17,61,.35); }
  .date-card__time { font-size: 23px; color: var(--ink); line-height: 32px; }
  .venue {
    position: absolute; right: 48px; top: 1052px; text-align: right;
    font-family: "Fira Sans", sans-serif; font-weight: 700;
  }
  .venue__name { font-size: 23px; color: var(--crimson); line-height: 30px; }
  .venue__address { font-size: 21px; color: var(--ink); line-height: 30px; }
</style>
</head>
<body>
<main class="flyer">
  <div class="butterflies butterflies--left" role="img" aria-label="Scattered golden butterflies fluttering upward"></div>
  <div class="butterflies butterflies--right" role="img" aria-label="Scattered golden butterflies fluttering upward"></div>

  <header class="brand">
    <span class="brand__dot"></span>
    <div class="brand__name">Brightwing Dance Studio</div>
  </header>

  <p class="presents">PRESENTS</p>

  <h1 class="recital-title">
    <span class="recital-title__ordinal">Our 11 th</span>
    <span class="recital-title__name">Annual Recital</span>
  </h1>

  <div class="ribbon-art" role="img" aria-label="Red satin ribbon looped into a heart shape around a faint grey world map"></div>

  <h2 class="theme">
    <span class="theme__line1">Where The River</span>
    <span class="theme__line2">Bends Home...</span>
  </h2>

  <section class="date-card">
    <div class="date-card__day">
      <svg style="left:16px" width="24" height="24" viewBox="0 0 24 24"><circle cx="12" cy="12" r="10" fill="#5e0a26"/><circle cx="12" cy="12" r="6" fill="#c2264f"/></svg>
      SATURDAY
      <svg style="right:16px" width="24" height="24" viewBox="0 0 24 24"><circle cx="12" cy="12" r="10" fill="#5e0a26"/><circle cx="12" cy="12" r="6" fill="#c2264f"/></svg>
    </div>
    <div class="date-card__date">JUNE 25, 2022</div>
    <div class="date-card__rule"></div>
    <div class="date-card__time">AT 4 PM</div>
  </section>

  <address class="venue" style="font-style:normal">
    <div class="venue__name">KESTREL RIDGE HIGH SCHOOL</div>
    <div class="venue__address">31857 Marlow Road Novi, Mi 48291</div>
  </address>
</main>
</body>
</html>
```